One pager digital ad-Corporate travel Manager

I need a design that is smooth, and business like. I don’t like basic generic designs that I can make my self. I’m looking for a sharp clean ad that clearly was made by a great designer. I need some bullet points in and the add to be clean. Here is a list of some content from our content writers. You can arrange and play with the words a bit.

*Budget*- having a travel management service will ensure that your company sticks to a budget which will help PROTECT your bottom line. Travel expenses often CAN BE COSTLY and having a SAVVY corporate travel manager handle YOUR TRAVEL ARRANGEMENTS will make sure that the travel expenses are kept under control.
*Efficiency- time *is money. Have your staff focus on their core business and have the corporate travel manager handle all the logistics for their travel including airfare, hotel cars and events TO MAXIMIZE EFFICIENCY AND KEEP YOUR STAFF FOCUSED ON YOUR CORE BUSINESS

*unforeseen circumstances* – the corporate travel manager handleS any cancellations, missed flights, canceled flights. Quick rebooking, and repositioning, and dealing with getting credits and reimbursement is extremely difficult and time-consuming. The corporate travel manager handles all of that SO YOU CAN CONTINUE ON SCHEDULE WITHOUT SPENDING HOURS REBOOKING AND GETTING CREDIT

Efficient and organized business travel management-help reduce travel expenses, streamline expense reports, optimize booking processes, and make managing the corporate travel experience way easier for all stakeholders involved.

Travel Support

Report on travel spend: In order to optimize their budgets, businesses need to know which departments are spending what on travel. Agencies can report on spend for all stakeholders by team, department, or project, and help you accurately track all your travel expenses.

Maintain compliance: Every company has some sort of rules that make up their travel policy. An agency can enforce these guidelines when booking.

Velnor Trips is a global leader in business travel management services. We drive savings, efficiency and safety to businesses and their travelers all around the world.

If you are looking for a tailored travel management solution, delivering customer service excellence, and a demonstrable return on investment, then you’ve come to the right place

Corporate travel policy compliance
Travel management reports
Meetings and event management
Travel program management
Dedicated travel counselor teams

By listening to your needs and focusing on your goals we can help your company design a global corporate travel service program that controls costs, improves traveler satisfaction and fits your corporate culture.

Our qualified business travel agents and cutting-edge technology deliver solutions that provide the best travel arrangements and travel policy adherence in the business. From CEO to support staff, our services can help make corporate travel a more efficient and enjoyable experience for everyone involved.

With so much involved in travel – from booking and expenses to meetings and strategy – you need the backing of a proven leader…
Velnor Trips, We’re your corporate travel partner to help you manage it all.

```html
<!DOCTYPE html>
<html lang="en">
<head>
<meta charset="UTF-8">
<title>Velnor Trips – Corporate Travel Flyer</title>
<link href="https://fonts.googleapis.com/css2?family=Poppins:wght@300;400;500;600;700;800&display=swap" rel="stylesheet">
<style>
:root{
  --navy:#0c1a3d;
  --gold:#e9a908;
  --ink:#1b1b1b;
  --white:#ffffff;
  --pill:#ececec;
}
*{margin:0;padding:0;box-sizing:border-box}
html,body{width:783px;height:1200px;overflow:hidden;background:#fff}
body{font-family:'Poppins',sans-serif;color:var(--ink)}
.flyer{position:relative;width:783px;height:1200px;overflow:hidden;background:var(--white)}
.hero-art{position:absolute;left:0;top:0}
.brand{position:absolute;left:40px;top:50px;width:140px;text-align:center;color:var(--white)}
.brand-mark{display:block;width:16px;height:16px;border-radius:50%;border:1.5px solid var(--white);margin:0 auto 6px}
.brand-name{font-size:10px;font-weight:500;letter-spacing:1.5px;text-transform:uppercase}
.hero-title{position:absolute;left:55px;top:104px;color:var(--white);font-weight:800;font-size:54px;line-height:52px;letter-spacing:.5px;text-transform:uppercase}
.hero-tagline{position:absolute;left:55px;top:224px;color:var(--white);text-transform:uppercase}
.hero-tagline .light{display:block;font-weight:300;font-size:18.5px;line-height:22px}
.hero-tagline .bold{display:block;font-weight:700;font-size:15.5px;line-height:20px}
.hero-rule{position:absolute;left:55px;top:281px;width:46px;height:4px;border-radius:2px;background:var(--gold)}
.hero-lead{position:absolute;left:55px;top:300px;width:300px;color:var(--white);font-weight:600;font-size:12.5px;line-height:15px}

.col{position:absolute;font-size:10.3px;line-height:12.6px}
.col p{text-align:justify;margin-bottom:6px}
.col-left{left:55px;top:388px;width:315px}
.col-right{left:414px;top:398px;width:318px}
.point-title{font-size:13.5px;font-weight:700;color:var(--navy);margin:0 0 4px;text-transform:uppercase}
.point + .point{margin-top:10px}
.photos{position:absolute;left:55px;top:812px;display:flex;gap:35px}
.photo{width:140px;height:80px;border:3px solid #fff;box-shadow:0 1px 4px rgba(0,0,0,.35)}
.photo-coast{background:linear-gradient(160deg,#4a7891 0%,#6f9aa8 35%,#a7b35a 65%,#6b7d2f 100%)}
.photo-summit{background:linear-gradient(180deg,#3d6fb5 0%,#9cbbe0 45%,#e9d9bd 60%,#5a6478 100%)}

.section-title{font-size:23px;font-weight:700;color:var(--gold);line-height:26px;text-transform:uppercase;margin-bottom:4px}
.sub-title{font-size:13.5px;font-weight:700;color:var(--navy);text-transform:uppercase;margin:10px 0 3px}
.sub-title.first{margin-top:0}
.about-box{background:var(--navy);color:var(--white);border-radius:7px;padding:9px 16px;font-size:11.8px;line-height:14px;margin:12px 2px 14px 4px}
.about-box strong{font-weight:700}
.tailored-title{font-size:12.3px;font-weight:700;color:var(--navy);text-transform:uppercase}
.benefits{display:flex;justify-content:space-between;margin:8px 0 6px}
.benefit{width:106px;text-align:center;font-size:10.5px;font-weight:600;line-height:12.5px;color:var(--navy)}
.benefit-icon{display:block;width:32px;height:32px;margin:0 auto 4px}
.pill{background:var(--pill);border-radius:10px;text-align:center;font-size:13px;line-height:22px;color:var(--ink);margin:4px 0 0 2px}

.services{position:absolute;left:39px;top:932px;width:705px;height:77px;background:var(--gold);border-radius:6px;display:flex;justify-content:space-around;padding:0 14px}
.service{position:relative;width:130px;text-align:center;font-size:11px;font-weight:600;line-height:13px;color:var(--navy);padding-top:34px}
.service-icon{position:absolute;left:50%;top:-26px;margin-left:-23px;width:46px;height:46px}

.closing{position:absolute;top:1025px;width:315px;font-size:10.3px;line-height:12.6px;text-align:justify}
.closing-left{left:55px}
.closing-right{left:416px}

.footer-art{position:absolute;left:0;top:1108px}
.contact{position:absolute;top:1140px;display:flex;align-items:center;gap:5px;font-size:18.5px;color:var(--white);line-height:24px}
.contact svg{width:17px;height:17px}
.contact-phone{left:52px}
.contact-mail{left:210px}
.contact-web{left:522px;color:var(--ink)}
</style>
</head>
<body>
<main class="flyer">

  <svg class="hero-art" width="783" height="420" viewBox="0 0 783 420" aria-hidden="false">
    <rect x="0" y="0" width="783" height="375" fill="var(--navy)"/>
    <path d="M600,0 H783 V375 H520 C640,365 760,290 772,160 C777,90 740,30 690,0 Z" fill="var(--white)"/>
    <circle cx="560" cy="165" r="194" fill="var(--white)"/>
    <defs>
      <linearGradient id="heroSky" x1="0" y1="0" x2="0" y2="1">
        <stop offset="0" stop-color="#8fb4d8"/>
        <stop offset="0.45" stop-color="#b9cfe2"/>
        <stop offset="0.6" stop-color="#5d6f86"/>
        <stop offset="0.78" stop-color="#7d7a48"/>
        <stop offset="1" stop-color="#5c5a2c"/>
      </linearGradient>
    </defs>
    <circle cx="560" cy="165" r="186" fill="url(#heroSky)" role="img" aria-label="Photo of a traveller with a backpack raising his arms on a mountain top overlooking a valley"/>
    <path d="M389,289 C440,370 580,380 650,330 C715,285 748,220 742,160 C722,245 640,318 530,322 C470,324 420,312 389,289 Z" fill="var(--gold)"/>
  </svg>

  <div class="brand">
    <span class="brand-mark"></span>
    <span class="brand-name">Velnor Trips</span>
  </div>

  <h1 class="hero-title">Velnor<br>Trips</h1>
  <p class="hero-tagline">
    <span class="light">We’re your corporate travel</span>
    <span class="bold">partner to help you manage it all</span>
  </p>
  <span class="hero-rule"></span>
  <p class="hero-lead">With so much involved in travel – from booking and expenses to meetings and strategy – you need the backing of a proven leader…</p>

  <section class="col col-left">
    <div class="point">
      <h3 class="point-title">*Budget*</h3>
      <p>having a travel management service will ensure that your company sticks to a budget which will help PROTECT your bottom line. Travel expenses often CAN BE COSTLY and having a SAVVY corporate travel manager handle YOUR TRAVEL ARRANGEMENTS will make sure that the travel expenses are kept under control.</p>
    </div>
    <div class="point">
      <h3 class="point-title">*Efficiency</h3>
      <p>time *is money. Have your staff focus on their core business and have the corporate travel manager handle all the logistics for their travel including airfare, hotel cars and events TO MAXIMIZE EFFICIENCY AND KEEP YOUR STAFF FOCUSED ON YOUR CORE BUSINESS</p>
    </div>
    <div class="point">
      <h3 class="point-title">*Unforeseen circumstances*</h3>
      <p>the corporate travel manager handleS any cancellations, missed flights, canceled flights. Quick rebooking, and repositioning, and dealing with getting credits and reimbursement is extremely difficult and time-consuming. The corporate travel manager handles all of that SO YOU CAN CONTINUE ON SCHEDULE WITHOUT SPENDING HOURS REBOOKING AND GETTING CREDIT</p>
      <p>Efficient and organized business travel management-help reduce travel expenses, streamline expense reports, optimize booking processes, and make managing the corporate travel experience way easier for all stakeholders involved.</p>
    </div>
  </section>

  <div class="photos">
    <div class="photo photo-coast" role="img" aria-label="Aerial photo of a green coastline with waves breaking on rocks"></div>
    <div class="photo photo-summit" role="img" aria-label="Photo of a hiker standing on a snowy summit above the clouds"></div>
  </div>

  <section class="col col-right">
    <h2 class="section-title">Travel Support</h2>
    <h3 class="sub-title first">Report on travel spend</h3>
    <p>In order to optimize their budgets, businesses need to know which departments are spending what on travel. Agencies can report on spend for all stakeholders by team, department, or project, and help you accurately track all your travel expenses.</p>
    <h3 class="sub-title">Maintain compliance</h3>
    <p>Every company has some sort of rules that make up their travel policy. An agency can enforce these guidelines when booking.</p>
    <h3 class="sub-title">Maintain compliance</h3>
    <p>Every company has some sort of rules that make up their travel policy. An agency can enforce these guidelines when booking.</p>
    <div class="about-box"><strong>Velnor Trips</strong> is a global leader in business travel management services. We drive savings, efficiency and safety to businesses and their travelers all around the world.</div>
    <h3 class="tailored-title">If you are looking for a tailored travel</h3>
    <div class="benefits">
      <div class="benefit">
        <svg class="benefit-icon" viewBox="0 0 32 32"><circle cx="16" cy="16" r="15" fill="var(--gold)"/><circle cx="16" cy="16" r="6" fill="none" stroke="#fff" stroke-width="1.6"/><circle cx="16" cy="16" r="2" fill="#fff"/></svg>
        Management<br>solution
      </div>
      <div class="benefit">
        <svg class="benefit-icon" viewBox="0 0 32 32"><circle cx="16" cy="16" r="15" fill="var(--gold)"/><rect x="10" y="9" width="12" height="14" rx="1.5" fill="none" stroke="#fff" stroke-width="1.6"/><path d="M13 16l2 2 4-4" fill="none" stroke="#fff" stroke-width="1.6"/></svg>
        Delivering<br>customer<br>service excellence
      </div>
      <div class="benefit">
        <svg class="benefit-icon" viewBox="0 0 32 32"><circle cx="16" cy="16" r="15" fill="var(--gold)"/><path d="M9 22h14M11 22v-4M15 22v-7M19 22v-10" fill="none" stroke="#fff" stroke-width="1.8"/></svg>
        Demonstrable<br>return on<br>investment
      </div>
    </div>
    <p class="pill">Then you’ve come to the right place</p>
  </section>

  <section class="services">
    <div class="service">
      <svg class="service-icon" viewBox="0 0 46 46"><circle cx="23" cy="23" r="21" fill="#fff" stroke="var(--gold)" stroke-width="2.5"/><circle cx="23" cy="23" r="17" fill="none" stroke="var(--gold)" stroke-width="1" stroke-dasharray="2 2"/><rect x="16" y="15" width="14" height="16" rx="1.5" fill="none" stroke="var(--navy)" stroke-width="1.4"/><path d="M19 20h8M19 24h8M19 28h5" stroke="var(--navy)" stroke-width="1.3"/></svg>
      Corporate travel<br>policy compliance
    </div>
    <div class="service">
      <svg class="service-icon" viewBox="0 0 46 46"><circle cx="23" cy="23" r="21" fill="#fff" stroke="var(--gold)" stroke-width="2.5"/><circle cx="23" cy="23" r="17" fill="none" stroke="var(--gold)" stroke-width="1" stroke-dasharray="2 2"/><path d="M16 30h14M18 30v-5M23 30v-9M28 30v-7" stroke="var(--navy)" stroke-width="1.8"/></svg>
      Travel management<br>reports
    </div>
    <div class="service">
      <svg class="service-icon" viewBox="0 0 46 46"><circle cx="23" cy="23" r="21" fill="#fff" stroke="var(--gold)" stroke-width="2.5"/><circle cx="23" cy="23" r="17" fill="none" stroke="var(--gold)" stroke-width="1" stroke-dasharray="2 2"/><rect x="15" y="16" width="16" height="14" rx="1.5" fill="none" stroke="var(--navy)" stroke-width="1.4"/><path d="M15 20h16M19 14v4M27 14v4" stroke="var(--navy)" stroke-width="1.4"/></svg>
      Meetings and event<br>management
    </div>
    <div class="service">
      <svg class="service-icon" viewBox="0 0 46 46"><circle cx="23" cy="23" r="21" fill="#fff" stroke="var(--gold)" stroke-width="2.5"/><circle cx="23" cy="23" r="17" fill="none" stroke="var(--gold)" stroke-width="1" stroke-dasharray="2 2"/><rect x="15" y="16" width="16" height="11" rx="1" fill="none" stroke="var(--navy)" stroke-width="1.4"/><path d="M19 31h8M23 27v4M18 24l4-3 3 2 4-4" fill="none" stroke="var(--navy)" stroke-width="1.3"/></svg>
      Travel program<br>management
    </div>
    <div class="service">
      <svg class="service-icon" viewBox="0 0 46 46"><circle cx="23" cy="23" r="21" fill="#fff" stroke="var(--gold)" stroke-width="2.5"/><circle cx="23" cy="23" r="17" fill="none" stroke="var(--gold)" stroke-width="1" stroke-dasharray="2 2"/><circle cx="18" cy="20" r="2.5" fill="none" stroke="var(--navy)" stroke-width="1.3"/><circle cx="28" cy="20" r="2.5" fill="none" stroke="var(--navy)" stroke-width="1.3"/><circle cx="23" cy="18" r="2.8" fill="none" stroke="var(--navy)" stroke-width="1.3"/><path d="M14 29c0-4 8-4 8 0M24 29c0-4 8-4 8 0M18 27c0-5 10-5 10 0" fill="none" stroke="var(--navy)" stroke-width="1.3"/></svg>
      Dedicated travel<br>counselor teams
    </div>
  </section>

  <p class="closing closing-left">Our qualified business travel agents and cutting-edge technology deliver solutions that provide the best travel arrangements and travel policy adherence in the business. From CEO to support staff, our services can help make corporate travel a more efficient and enjoyable experience for everyone involved.</p>
  <p class="closing closing-right">Our qualified business travel agents and cutting-edge technology deliver solutions that provide the best travel arrangements and travel policy adherence in the business. From CEO to support staff, our services can help make corporate travel a more efficient and enjoyable experience for everyone involved.</p>

  <svg class="footer-art" width="783" height="92" viewBox="0 0 783 92" aria-hidden="true">
    <path d="M0,7 H470 C520,7 540,30 560,92 H0 Z" fill="var(--navy)"/>
    <path d="M470,7 C525,5 548,28 568,92 H580 C560,30 540,2 470,0 Z" fill="var(--gold)"/>
  </svg>

  <p class="contact contact-phone">
    <svg viewBox="0 0 20 20"><path d="M5 2l3 3-2 3c1 2 3 4 5 5l2-2 3 3-2 3C8 17 3 12 2 5z" fill="var(--gold)"/></svg>
    012.555.0148
  </p>
  <p class="contact contact-mail">
    <svg viewBox="0 0 20 20"><rect x="2" y="4" width="16" height="12" rx="1" fill="var(--gold)"/><path d="M2 5l8 6 8-6" fill="none" stroke="var(--navy)" stroke-width="1.4"/></svg>
    hello@velnortrips.com
  </p>
  <p class="contact contact-web">
    <svg viewBox="0 0 20 20"><circle cx="10" cy="10" r="8" fill="none" stroke="var(--navy)" stroke-width="1.5"/><ellipse cx="10" cy="10" rx="3.5" ry="8" fill="none" stroke="var(--navy)" stroke-width="1.3"/><path d="M2 10h16M3.5 6h13M3.5 14h13" stroke="var(--navy)" stroke-width="1.2"/></svg>
    www.velnortrips.com
  </p>

</main>
</body>
</html>
```